Business card design Needed for new logo / Construction business, home extensions and new builds

We need a business card design using our new logo files which i will attach to this project :)

We are a small construction business specialising in home extensions, new builds and property development. We are very ambitious and would appreciate professional and elegant designs for our new business card.

Very serious about using the services on MakerQuarry and recently acquired our new logo from here :)

Please get involved, i will feedback when i can as i am very busy but can respond daily, thanks

Target Market(s)

People that want to build onto their houses, new building developments or adding too their existing property

Industry/Entity Type

Construction

Contact Information for Business Card

Renwick Tolliver Construction, Lionel Ashby (Managing Director), Tel 07822254961, email - info@renwick-tolliver, www.renwick-tolliver.co.uk

Colors

Designer to choose colors to be used in the design.

Requirements
Must have
• I like a deep grey on the back please. A lot of you have provided black from and back, try mixing things up a little. The black looks cool 😎 Thanks

```html
<!DOCTYPE html>
<html lang="en">
<head>
<meta charset="utf-8">
<title>Renwick Tolliver Construction – Business Card</title>
<link href="https://fonts.googleapis.com/css2?family=Open+Sans:wght@400;600;700&display=swap" rel="stylesheet">
<style>
  :root {
    --stage: #2a2a2e;
    --card-black: #1c1c20;
    --card-deep: #232327;
    --silver: #d4d6da;
    --silver-dark: #9a9ca2;
    --gold-light: #f3d27a;
    --gold: #d9a53a;
    --gold-dark: #a8771c;
    --text-light: #f4f4f4;
    --band-text: #fff9ea;
  }
  * { margin: 0; padding: 0; box-sizing: border-box; }
  html, body { width: 1200px; height: 780px; overflow: hidden; }
  body {
    background: var(--stage);
    font-family: "Open Sans", Arial, sans-serif;
    display: flex;
    align-items: center;
    justify-content: center;
    gap: 40px;
  }
  .card {
    position: relative;
    width: 560px;
    height: 320px;
    overflow: hidden;
    box-shadow: 0 14px 30px rgba(0,0,0,0.45);
  }

  /* Back */
  .card-back { background: var(--card-deep); }
  .back-pattern {
    position: absolute; inset: 0;
    background: linear-gradient(135deg, #3a3a3f 0%, #2a2a2f 35%, #1e1e22 70%, #18181b 100%);
  }
  .back-mark {
    position: absolute; right: 26px; bottom: 128px;
    display: flex; align-items: center; gap: 5px;
    color: var(--silver);
    font-size: 7px; font-weight: 600; letter-spacing: 0.5px; text-transform: uppercase;
  }
  .back-mark .mark-square { width: 7px; height: 7px; background: var(--gold); }

  /* Front */
  .card-front { background: var(--card-black); }
  .brand {
    position: absolute; left: 60px; top: 70px;
    display: flex; align-items: center; gap: 10px;
  }
  .brand .mark-square {
    width: 34px; height: 34px;
    background: linear-gradient(180deg, var(--gold-light), var(--gold-dark));
  }
  .brand-name {
    color: var(--silver);
    font-size: 15px; font-weight: 600;
    letter-spacing: 1.5px; text-transform: uppercase; line-height: 1.35;
    width: 190px;
  }
  .person { position: absolute; left: 40px; top: 178px; }
  .person-name {
    font-size: 36px; font-weight: 700; line-height: 1; letter-spacing: 0.5px;
  }
  .person-name .first { color: var(--silver); }
  .person-name .last { color: var(--gold); }
  .person-title {
    margin-top: 4px; margin-left: 88px;
    color: var(--text-light); font-size: 15px; font-weight: 600;
  }
  .divider {
    position: absolute; left: 318px; top: 150px;
    width: 1px; height: 78px;
    background: linear-gradient(180deg, transparent, var(--silver-dark), transparent);
  }
  .contacts {
    position: absolute; left: 334px; top: 88px;
    list-style: none;
  }
  .contacts li {
    display: flex; align-items: center; gap: 8px;
    color: var(--text-light); font-size: 13.5px; line-height: 24px;
  }
  .contacts svg { width: 13px; height: 13px; flex: none; }
  .address-band {
    position: absolute; left: 0; right: 0; top: 264px; height: 24px;
    background: linear-gradient(180deg, var(--gold-light) 0%, var(--gold) 45%, var(--gold-dark) 100%);
    display: flex; align-items: center; justify-content: center;
    color: var(--band-text); font-size: 12.5px; font-weight: 600; letter-spacing: 0.3px;
  }
</style>
</head>
<body>

  <section class="card card-back" aria-label="Card back">
    <div class="back-pattern" role="img" aria-label="Repeating monogram pattern in tonal black and silver"></div>
    <div class="back-mark"><span class="mark-square"></span>Renwick Tolliver Construction</div>
  </section>

  <section class="card card-front" aria-label="Card front">
    <div class="brand">
      <span class="mark-square"></span>
      <span class="brand-name">Renwick Tolliver Construction</span>
    </div>

    <div class="person">
      <p class="person-name"><span class="first">Lionel</span> <span class="last">Ashby</span></p>
      <p class="person-title">Managing Director</p>
    </div>

    <div class="divider"></div>

    <ul class="contacts">
      <li>
        <svg viewBox="0 0 16 16" aria-hidden="true"><path fill="#d9a53a" d="M3.5 1.5l2.5 0 1 3.5-1.6 1.2a8 8 0 0 0 4.4 4.4L11 9l3.5 1v2.5c0 .8-.7 1.5-1.5 1.5C7 14 2 9 2 3c0-.8.7-1.5 1.5-1.5z"/></svg>
        0782 225 4961
      </li>
      <li>
        <svg viewBox="0 0 16 16" aria-hidden="true"><rect x="1.5" y="3.5" width="13" height="9" rx="1" fill="#d9a53a"/><path d="M2 4l6 5 6-5" fill="none" stroke="#1c1c20" stroke-width="1.2"/></svg>
        info@renwick-tolliver.co.uk
      </li>
      <li>
        <svg viewBox="0 0 16 16" aria-hidden="true"><circle cx="8" cy="8" r="6.5" fill="#d9a53a"/><path d="M1.5 8h13M8 1.5c-3 3.5-3 9.5 0 13M8 1.5c3 3.5 3 9.5 0 13" fill="none" stroke="#1c1c20" stroke-width="1"/></svg>
        www.renwick-tolliver.co.uk
      </li>
    </ul>

    <div class="address-band">Harlow Lane, Ashcombe Westmere, WM4 7QT</div>
  </section>

</body>
</html>
```